Law Firm Header Revision

Task: Redesign my law firm Word document header (modern, succinct, logo-first, easy address updates)

I need you to revise and modernize my Microsoft Word document header for Law Office of Bram Holcott, PLLC. The result should look professional and clean on letters (including Letters of Protection), with the logo as the main focus and the text kept succinct.

Goals:
1. Create a modern, minimal header that feels premium and uncluttered.
Make the logo the most visually dominant element.
Reduce the visual weight of the contact/address block so it doesn’t distract from the document.
Make the address easy to change later (I’m moving offices soon) while keeping the same header design.

2. Content to include (keep all info accurate):
Law Office of Bram Holcott, PLLC
615 Pemberly St. Ste #300-214, Houston, TX 77002
Office: 832.555.0143
Direct: 713.555.0187
Fax: 832.555.0129
Bholcottlaw.com

3. Layout requirements:
Provide 3 header style options:
Logo left + contact info right
Centered logo + single concise contact line below
Logo left + firm name prominent + minimal contact line
The primary line near the logo should be minimal (preferably website + main office phone).
The address should be easy to update in one place without redesigning the header. Prefer either:
Move the full address to the footer, or
Put the address in a single dedicated line/block so I can edit it once and keep the layout unchanged.
4. Build constraints:
Must be achievable using standard Microsoft Word tools only (header/footer, tables, alignment, fonts, spacing). No advanced graphics software.
Provide exact header text, plus step-by-step Word instructions for each option:
Font recommendations + sizes
Alignment
Spacing
Table setup (if used)
How to keep it consistent across pages

5. Deliverable:
For each of the 3 options, provide:
The exact header content (with line breaks)
Formatting specs (fonts, sizes, spacing)
Word build steps so I can recreate it reliably and keep the logo as the focal point.

```html
<!DOCTYPE html>
<html lang="en">
<head>
<meta charset="utf-8">
<title>Bram Holcott Law – Letterhead Options</title>
<link rel="stylesheet" href="https://fonts.googleapis.com/css2?family=Josefin+Sans:wght@400;600&family=Playfair+Display:wght@400;500&family=Tinos&display=swap">
<style>
  :root{
    --navy:#0d1623;
    --paper:#ffffff;
    --canvas:#ffffff;
    --panel:#f2f3f5;
    --ink:#1d2430;
  }
  *{box-sizing:border-box;margin:0;padding:0}
  html,body{width:1200px;height:533px;overflow:hidden;background:var(--canvas)}
  .sheet{
    position:absolute;top:31px;width:780px;height:1008px;
    background:var(--paper);
    transform:scale(.4667);transform-origin:0 0;
    box-shadow:0 0 6px rgba(0,0,0,.18);
    overflow:hidden;
  }
  .sheet--one{left:31px}
  .sheet--two{left:419px}
  .sheet--three{left:807px}
  .frame{position:absolute;inset:0;width:780px;height:1008px}

  .mark{position:absolute;width:63px;height:63px;background:var(--navy)}
  .wordmark{position:absolute;width:215px;color:var(--navy);text-align:center}
  .wordmark__name{
    display:block;font-family:"Playfair Display",serif;font-weight:400;
    font-size:44px;line-height:44px;white-space:nowrap;
    transform:scaleX(.66);transform-origin:center;
    width:330px;margin-left:-57px;
  }
  .wordmark__sub{
    display:flex;align-items:center;gap:10px;margin-top:4px;
    font-family:"Tinos",serif;font-size:18px;letter-spacing:6px;line-height:18px;
  }
  .wordmark__sub::before,.wordmark__sub::after{content:"";flex:1;height:1.5px;background:var(--navy)}

  .firm-name{
    position:absolute;left:63px;top:152px;
    font-family:"Tinos",serif;font-size:19px;color:var(--ink);letter-spacing:.3px;
  }

  .icon{width:22px;height:22px;background:var(--navy);display:inline-flex;align-items:center;justify-content:center;flex:none}
  .icon svg{width:11px;height:11px;fill:#fff}
  .contact{
    display:flex;align-items:center;gap:14px;
    font-family:"Josefin Sans",sans-serif;font-size:12.5px;color:var(--ink);letter-spacing:.2px;white-space:nowrap;
  }
  .stack{position:absolute;right:59px;top:70px;display:flex;flex-direction:column;align-items:flex-end;gap:21px}
  .stack .contact{gap:16px}
  .stack-rule{position:absolute;left:733px;top:65px;width:1.5px;height:76px;background:var(--navy)}

  .line{position:absolute;top:166px;left:225px;display:flex;align-items:center}
  .line .divider{width:1.5px;height:34px;background:var(--navy);margin:0 40px 0 31px}

  .watermark{position:absolute;width:542px;height:518px;background:var(--panel);left:119px;top:245px}
  .sheet--two .watermark{top:294px}

  .footer{position:absolute;left:29px;top:933px;display:flex;align-items:center}
  .footer .contact{margin-right:0}
  .footer .c1{width:163px}
  .footer .c2{width:165px}
  .footer-tag{
    position:absolute;right:54px;top:985px;
    font-family:"Josefin Sans",sans-serif;font-size:9.5px;color:#fff;letter-spacing:.3px;white-space:nowrap;
  }
  .footer-tag span{margin:0 8px}
</style>
</head>
<body>
<svg width="0" height="0" style="position:absolute" aria-hidden="true">
  <defs>
    <symbol id="i-phone" viewBox="0 0 24 24"><path d="M6.6 10.8a15.2 15.2 0 0 0 6.6 6.6l2.2-2.2c.3-.3.7-.4 1-.2 1.1.4 2.3.6 3.6.6.6 0 1 .4 1 1V20c0 .6-.4 1-1 1A17 17 0 0 1 3 4c0-.6.4-1 1-1h3.5c.6 0 1 .4 1 1 0 1.3.2 2.5.6 3.6.1.3 0 .7-.2 1z"/></symbol>
    <symbol id="i-globe" viewBox="0 0 24 24"><path d="M12 2a10 10 0 1 0 0 20 10 10 0 0 0 0-20zm6.9 6h-3a15.6 15.6 0 0 0-1.3-3.6A8 8 0 0 1 18.9 8zM12 4c.8 1.2 1.5 2.5 1.9 4h-3.8c.4-1.5 1.1-2.8 1.9-4zM4.3 14a8.2 8.2 0 0 1 0-4h3.4a16.500 16.500 0 0 0 0 4zm.8 2h3a15.600 15.600 0 0 0 1.3 3.6A8 8 0 0 1 5.1 16zm3-8h-3a8 8 0 0 1 4.3-3.6C8.800 5.500 8.400 6.700 8.100 8zM12 20c-.8-1.200-1.500-2.500-1.900-4h3.800c-.4 1.500-1.100 2.800-1.900 4zm2.300-6H9.700a14.700 14.700 0 0 1 0-4h4.600a14.700 14.700 0 0 1 0 4zm.300 5.600c.600-1.100 1-2.300 1.300-3.600h3a8 8 0 0 1-4.300 3.600zM16.300 14a16.500 16.500 0 0 0 0-4h3.400a8.200 8.200 0 0 1 0 4z"/></symbol>
    <symbol id="i-fax" viewBox="0 0 24 24"><path d="M7 3h10v4H7zM4 8h16a2 2 0 0 1 2 2v6h-4v5H6v-5H2v-6a2 2 0 0 1 2-2zm4 8v3h8v-3z"/></symbol>
    <symbol id="i-pin" viewBox="0 0 24 24"><path d="M12 2a7 7 0 0 0-7 7c0 5.200 7 13 7 13s7-7.800 7-13a7 7 0 0 0-7-7zm0 9.500A2.500 2.500 0 1 1 12 6.500a2.500 2.500 0 0 1 0 5z"/></symbol>
    <g id="corners">
      <polygon points="10,0 780,0 780,3 52,40" fill="#0d1623"/>
      <polygon points="0,4 44,40 0,84" fill="#0d1623"/>
      <polyline points="0,68 46,91 0,138" fill="none" stroke="#0d1623" stroke-width="1.5"/>
      <polygon points="0,1008 780,1008 780,1005 728,968" fill="#0d1623"/>
      <polygon points="780,918 735,966 780,1004" fill="#0d1623"/>
      <polyline points="780,868 731,911 758,940" fill="none" stroke="#0d1623" stroke-width="1.5"/>
    </g>
  </defs>
</svg>

<!-- Option 1: logo left, contact right -->
<section class="sheet sheet--one">
  <svg class="frame" viewBox="0 0 780 1008" aria-hidden="true"><use href="#corners"/></svg>
  <div class="mark" style="left:64px;top:70px"></div>
  <div class="wordmark" style="left:135px;top:73px"><span class="wordmark__name">BRAM HOLCOTT</span><span class="wordmark__sub">LAW</span></div>
  <div class="stack">
    <div class="contact">832.555.0143 <span class="icon"><svg><use href="#i-phone"/></svg></span></div>
    <div class="contact">BHOLCOTTLAW.COM <span class="icon"><svg><use href="#i-globe"/></svg></span></div>
  </div>
  <div class="stack-rule"></div>
  <div class="watermark" role="img" aria-label="Faint brand emblem watermark"></div>
  <div class="footer">
    <div class="contact c1"><span class="icon"><svg><use href="#i-phone"/></svg></span>713.555.0187</div>
    <div class="contact c2"><span class="icon"><svg><use href="#i-fax"/></svg></span>832.555.0129</div>
    <div class="contact"><span class="icon"><svg><use href="#i-pin"/></svg></span>615 PEMBERLY ST. STE #300-214 HOUSTON, TX 77002</div>
  </div>
  <div class="footer-tag">LETTER OF PROTECTION<span>|</span>PAGE 1</div>
</section>

<!-- Option 2: centered logo, single contact line -->
<section class="sheet sheet--two">
  <svg class="frame" viewBox="0 0 780 1008" aria-hidden="true"><use href="#corners"/></svg>
  <div class="mark" style="left:246px;top:68px"></div>
  <div class="wordmark" style="left:316px;top:71px"><span class="wordmark__name">BRAM HOLCOTT</span><span class="wordmark__sub">LAW</span></div>
  <div class="line">
    <div class="contact"><span class="icon"><svg><use href="#i-phone"/></svg></span>832.555.0143</div>
    <span class="divider"></span>
    <div class="contact"><span class="icon"><svg><use href="#i-globe"/></svg></span>BHOLCOTTLAW.COM</div>
  </div>
  <div class="watermark" role="img" aria-label="Faint brand emblem watermark"></div>
  <div class="footer">
    <div class="contact c1"><span class="icon"><svg><use href="#i-phone"/></svg></span>713.555.0187</div>
    <div class="contact c2"><span class="icon"><svg><use href="#i-fax"/></svg></span>832.555.0129</div>
    <div class="contact"><span class="icon"><svg><use href="#i-pin"/></svg></span>615 PEMBERLY ST. STE #300-214 HOUSTON, TX 77002</div>
  </div>
  <div class="footer-tag">LETTER OF PROTECTION<span>|</span>PAGE 1</div>
</section>

<!-- Option 3: logo left, firm name prominent -->
<section class="sheet sheet--three">
  <svg class="frame" viewBox="0 0 780 1008" aria-hidden="true"><use href="#corners"/></svg>
  <div class="mark" style="left:64px;top:70px"></div>
  <div class="wordmark" style="left:135px;top:73px"><span class="wordmark__name">BRAM HOLCOTT</span><span class="wordmark__sub">LAW</span></div>
  <div class="firm-name">LAW OFFICE OF BRAM HOLCOTT, PLLC</div>
  <div class="stack">
    <div class="contact">832.555.0143 <span class="icon"><svg><use href="#i-phone"/></svg></span></div>
    <div class="contact">BHOLCOTTLAW.COM <span class="icon"><svg><use href="#i-globe"/></svg></span></div>
  </div>
  <div class="stack-rule"></div>
  <div class="watermark" role="img" aria-label="Faint brand emblem watermark"></div>
  <div class="footer">
    <div class="contact c1"><span class="icon"><svg><use href="#i-phone"/></svg></span>713.555.0187</div>
    <div class="contact c2"><span class="icon"><svg><use href="#i-fax"/></svg></span>832.555.0129</div>
    <div class="contact"><span class="icon"><svg><use href="#i-pin"/></svg></span>615 PEMBERLY ST. STE #300-214 HOUSTON, TX 77002</div>
  </div>
  <div class="footer-tag">LETTER OF PROTECTION<span>|</span>PAGE 1</div>
</section>
</body>
</html>
```